Veldmark Supplies Business Card

Professional business card that stand out to our potential customers. Front and back with clean modern design

Industry/Entity Type

Oil and gas

Contact Information for Business Card

Name, address, website , office phone and cell number

Requirements
Must have
• Editable files for each employee

```html
<!DOCTYPE html>
<html lang="en">
<head>
<meta charset="utf-8">
<title>Veldmark Supplies Business Card</title>
<link rel="stylesheet" href="https://fonts.googleapis.com/css2?family=Exo+2:wght@400;800&family=Ubuntu:wght@400;500&display=swap">
<style>
  :root {
    --stage: #3a3a3c;
    --card: #1c1c1e;
    --card-back: #111112;
    --red: #ff0a0a;
    --cyan: #00b3d6;
    --white: #f2f2f2;
  }
  * { box-sizing: border-box; margin: 0; padding: 0; }
  html, body { width: 1200px; height: 694px; overflow: hidden; }
  body {
    background: var(--stage);
    display: flex;
    align-items: center;
    justify-content: center;
    gap: 40px;
    font-family: "Ubuntu", sans-serif;
  }
  .card {
    position: relative;
    width: 540px;
    height: 309px;
    border-radius: 18px;
    overflow: hidden;
    box-shadow: 0 10px 30px rgba(0,0,0,.45);
  }

  /* Back side */
  .card-back { background: var(--card-back); }
  .card-back .pattern {
    position: absolute; inset: 0;
    background: radial-gradient(ellipse at 45% 40%, #0b0b0c 0%, #1a1a1b 55%, #2a2a2b 100%);
  }
  .card-back .center-mark {
    position: absolute; inset: 0;
    display: flex; align-items: center; justify-content: center; gap: 8px;
  }
  .wordmark-square { width: 12px; height: 12px; background: var(--red); }
  .card-back .wordmark {
    font-family: "Exo 2", sans-serif; font-weight: 800;
    font-size: 15px; letter-spacing: 1px; text-transform: uppercase;
    color: var(--red);
  }

  /* Front side */
  .card-front { background: var(--card); }
  .brand {
    position: absolute; left: 34px; top: 0; width: 228px; height: 290px;
    display: flex; flex-direction: column; align-items: center; justify-content: center; gap: 12px;
  }
  .brand .wordmark-square { width: 40px; height: 40px; }
  .brand .wordmark {
    font-family: "Exo 2", sans-serif; font-weight: 800;
    font-size: 22px; letter-spacing: 1px; text-transform: uppercase;
    color: var(--red); text-align: center; line-height: 1.15;
  }
  .divider {
    position: absolute; left: 280px; top: 44px; width: 1px; height: 190px;
    background: linear-gradient(var(--red), rgba(255,10,10,.6));
  }
  .details { position: absolute; left: 302px; top: 46px; color: var(--white); }
  .person-name {
    font-family: "Exo 2", sans-serif; font-weight: 800;
    font-size: 25px; color: var(--red); line-height: 1;
  }
  .person-role { font-size: 13px; color: var(--cyan); margin-top: 4px; }
  .address { font-size: 12.5px; line-height: 1.4; margin-top: 12px; }
  .contacts { list-style: none; margin-top: 12px; }
  .contacts li {
    display: flex; align-items: center; gap: 9px;
    font-size: 12.5px; line-height: 1; height: 19px;
  }
  .contacts svg { width: 13px; height: 13px; fill: var(--cyan); flex: none; }
  .stripe {
    position: absolute; left: 0; right: 0; bottom: 0; height: 7px;
    background: linear-gradient(90deg, var(--red) 0 78%, var(--cyan) 78% 100%);
  }
</style>
</head>
<body>

  <section class="card card-back" aria-label="Card back">
    <div class="pattern" role="img" aria-label="Embossed repeating monogram pattern in gloss black"></div>
    <div class="center-mark">
      <span class="wordmark-square"></span>
      <span class="wordmark">Veldmark Supplies</span>
    </div>
  </section>

  <section class="card card-front" aria-label="Card front">
    <div class="brand">
      <span class="wordmark-square"></span>
      <span class="wordmark">Veldmark<br>Supplies</span>
    </div>
    <div class="divider"></div>
    <div class="details">
      <p class="person-name">Marcus Hale</p>
      <p class="person-role">Owner</p>
      <p class="address">87, Ridgeway Road<br>30718, Karoo Basin</p>
      <ul class="contacts">
        <li>
          <svg viewBox="0 0 24 24" aria-hidden="true"><path d="M6.6 10.8a15 15 0 0 0 6.6 6.6l2.2-2.2a1 1 0 0 1 1-.25 11.4 11.4 0 0 0 3.6.57 1 1 0 0 1 1 1V20a1 1 0 0 1-1 1A17 17 0 0 1 3 4a1 1 0 0 1 1-1h3.5a1 1 0 0 1 1 1c0 1.250.2 2.450.57 3.6a1 1 0 0 1-.25 1z"/></svg>
          061-555 010 200
        </li>
        <li>
          <svg viewBox="0 0 24 24" aria-hidden="true"><path d="M7 1h10a2 2 0 0 1 2 2v18a2 2 0 0 1-2 2H7a2 2 0 0 1-2-2V3a2 2 0 0 1 2-2zm0 3v14h10V4zm5 15.5a1 1 0 1 0 0 2 1 1 0 0 0 0-2z"/></svg>
          061-555 010 200
        </li>
        <li>
          <svg viewBox="0 0 24 24" aria-hidden="true"><path d="M2 5h20v14H2zm2 2v.5l8 5 8-5V7l-8 5z"/></svg>
          info@veldmarksupply.com
        </li>
        <li>
          <svg viewBox="0 0 24 24" aria-hidden="true"><path d="M12 2a10 10 0 1 0 0 20 10 10 0 0 0 0-20zm-1 17.9A8 8 0 0 1 4.1 10L9 15v1a2 2 0 0 0 2 2zm6.9-2.5A2 2 0 0 0 16 16h-1v-3a1 1 0 0 0-1-1H8v-2h2a1 1 0 0 0 1-1V7h2a2 2 0 0 0 2-2v-.4a8 8 0 0 1 2.9 12.8z"/></svg>
          www.veldmarksupply.com
        </li>
      </ul>
    </div>
    <div class="stripe"></div>
  </section>

</body>
</html>
```